Wilderness Doc & TV personality personal page

I’m a wilderness and EMS emergency physician with particular sub specialties and a TV show. I need a website to highlight my interviews, teachings, etc... I did buy a number of domains for now.
Topics and things I need: CV (or version) me in the media, picture gallery, actually I sort of really like what dr owen barkley, my colleague has setup plus I have tv show and stuff like that. ridgeway healer dot com

Target Market(s)

EMS, education, commercial products...

Industry/Entity Type

Medical And Science

Coding

Coded - Design and coding required

Number of Pages Required

1 page

Font styles to use
Sans Serif

Colors
f37122
9bcb3c
0556a4
a54499

Requirements
Must have
• Links and photos to news articles and things that mention me that I can add in.
Nice to have
• Maybe some snapshots of lecture reviews or patient thank you notes. Accolades so to speak
• I really appreciate how sharp it is. I would love to see Headings that resemble my friend's at ridgeway healer dot com. Home, experience, consulting, lectures, affiliates, contact... those are main subjects... I think media also and that will have the TV show stuff and articles written about me...then maybe at the bottom of main page also have splits for training, research, television, and maybe exploration
Should not have
• The medical symbol with two snakes... that means quack doctor

```html
<!DOCTYPE html>
<html lang="en">
<head>
<meta charset="utf-8">
<title>Ben Carver — Wilderness &amp; EMS Physician</title>
<link href="https://fonts.googleapis.com/css2?family=Lato:wght@400;700;900&display=swap" rel="stylesheet">
<style>
:root{
  --blue:#0556a4;
  --green:#9bcb3c;
  --purple:#a54499;
  --orange:#f37122;
  --ink:#2b2b2b;
  --text:#555;
  --band:#f1f1f1;
  --footer:#1f1f1f;
}
*{margin:0;padding:0;box-sizing:border-box}
html,body{width:1200px;height:2740px;overflow:hidden}
body{font-family:'Lato',sans-serif;color:var(--text);background:#fff;position:relative}
.site-header{position:absolute;top:0;left:0;width:1200px;height:90px;display:flex;align-items:center;justify-content:space-between;padding:0 70px;background:#fff}
.brand{font-size:34px;font-weight:900;color:var(--blue);letter-spacing:1px}
.main-nav{display:flex;gap:38px}
.main-nav a{font-size:14px;font-weight:700;color:var(--ink);text-decoration:none;letter-spacing:1px}
.main-nav a.active{color:var(--purple)}
.hero{position:absolute;top:90px;left:0;width:1200px;height:630px}
.hero-photo{position:absolute;inset:0;background:linear-gradient(90deg,#e9ede9 0%,#cfdcd6 35%,#6f9aa0 60%,#3f6f5f 100%)}
.hero-copy{position:absolute;left:70px;top:200px;width:560px}
.hero-copy .kicker{font-size:34px;font-weight:900;color:var(--ink)}
.hero-copy h1{font-size:64px;font-weight:900;color:var(--ink);line-height:1.05;margin-bottom:14px}
.hero-copy p{font-size:26px;font-weight:700;color:var(--purple);line-height:1.3;margin-bottom:30px}
.btn{display:inline-block;padding:16px 30px;font-size:14px;font-weight:700;color:#fff;letter-spacing:1px;text-decoration:none}
.btn-purple{background:var(--purple)}
.btn-green{background:var(--green)}
.about{position:absolute;top:720px;left:0;width:1200px;height:480px}
.round-photo{position:absolute;border-radius:50%}
.about .round-photo{left:100px;top:40px;width:360px;height:360px;background:radial-gradient(circle at 50% 40%,#d8c9a8,#7f9a4a 55%,#3c4a2d)}
.about-copy{position:absolute;left:520px;top:60px;width:600px}
.section-title{font-size:30px;font-weight:900;color:var(--ink);letter-spacing:.5px}
.credentials{font-size:18px;font-weight:700;color:var(--blue);margin:6px 0 18px}
.body-copy{font-size:16px;line-height:1.7;margin-bottom:28px}
.tv{position:absolute;top:1200px;left:0;width:1200px;height:540px;background:var(--band)}
.interview-card{position:absolute;left:70px;top:30px;width:330px;height:480px;background:var(--blue);padding:24px 20px}
.interview-card h2{color:#fff;font-size:28px;font-weight:900;line-height:1.15;text-align:center}
.interview-photo{position:absolute;left:20px;right:20px;bottom:20px;height:290px;background:linear-gradient(160deg,#5ea0d0,#2b6d9c 60%,#1c4a70)}
.tv-head{position:absolute;left:430px;top:30px;width:700px;display:flex;justify-content:space-between;align-items:center}
.tv-arrows{display:flex;gap:14px}
.show-card{position:absolute;top:90px;width:330px}
.show-photo{position:relative;height:220px}
.show-photo svg{position:absolute;left:50%;top:50%;transform:translate(-50%,-50%)}
.show-card h3{font-size:16px;font-weight:900;color:var(--purple);margin:18px 0 8px;letter-spacing:.5px}
.show-card p{font-size:14px;line-height:1.5}
.watch{display:block;margin-top:8px;font-size:12px;font-weight:700;color:var(--green);text-decoration:none;letter-spacing:1px}
.media{position:absolute;top:1740px;left:0;width:1200px;height:480px;background:linear-gradient(90deg,#fbeee8 0%,#f4d7cf 100%)}
.media-copy{position:absolute;left:70px;top:70px;width:620px}
.media-copy .section-title{margin-bottom:20px}
.media .round-photo{left:740px;top:60px;width:350px;height:350px;background:radial-gradient(circle at 50% 40%,#c9c6c0,#6c7f8f 55%,#2e3a45)}
.splits{position:absolute;top:2240px;left:70px;width:1060px;height:320px;display:flex;justify-content:space-between}
.split{position:relative;width:330px;height:300px;display:flex;align-items:center;justify-content:center;text-decoration:none}
.split span{position:relative;font-size:34px;font-weight:900;color:#fff;letter-spacing:1px}
.split-gallery{background:linear-gradient(150deg,#8d6b55,#4d3a30)}
.split-research{background:linear-gradient(150deg,#7f8a96,#3e4650)}
.split-television{background:linear-gradient(150deg,#7b5a44,#2f2520)}
.site-footer{position:absolute;top:2630px;left:0;width:1200px;height:110px;background:var(--footer);padding:28px 70px}
.footer-row{display:flex;justify-content:space-between;align-items:center}
.footer-nav{display:flex;gap:30px}
.footer-nav a{font-size:12px;font-weight:700;color:#fff;text-decoration:none;letter-spacing:1px}
.social{display:flex;gap:16px}
.social span{width:18px;height:18px;border-radius:50%;background:#bdbdbd;display:block}
.copyright{margin-top:24px;font-size:12px;color:#9a9a9a}
</style>
</head>
<body>
<header class="site-header">
  <div class="brand">BEN CARVER</div>
  <nav class="main-nav">
    <a class="active" href="#">HOME</a><a href="#">EXPERIENCE</a><a href="#">CONSULTING</a><a href="#">LECTURES</a><a href="#">AFFILIATES</a><a href="#">CONTACT</a>
  </nav>
</header>

<section class="hero">
  <div class="hero-photo" role="img" aria-label="Photo of the physician in scrubs with a stethoscope, arms crossed, standing outdoors by a waterfront"></div>
  <div class="hero-copy">
    <div class="kicker">WELCOME TO</div>
    <h1>BENJAMIN CARVER</h1>
    <p>I'm a wilderness and EMS emergency physician with particular sub specialties and a TV show.</p>
    <a class="btn btn-purple" href="#">READ MORE</a>
  </div>
</section>

<section class="about">
  <div class="round-photo" role="img" aria-label="Portrait of the physician in a fire rescue uniform in front of an ambulance"></div>
  <div class="about-copy">
    <h2 class="section-title">ABOUT BENJAMIN CARVER</h2>
    <div class="credentials">DO, EMT-P, FAWM</div>
    <p class="body-copy">Benjamin Carver, DO, EMT-P, FAWM, is an assistant professor of emergency medicine and EMS at Coastal State University. He's an active EMS physician with multiple departments in Florida, including medical director for Bayline Fire Rescue Task Force One USAR and very active globally in wilderness/austere EMS.</p>
    <a class="btn btn-green" href="#">READ MORE</a>
  </div>
</section>

<section class="tv">
  <div class="interview-card">
    <h2>INTERVIEW WITH<br>BENJAMIN CARVER</h2>
    <div class="interview-photo" role="img" aria-label="Video still of the physician during an interview"></div>
  </div>
  <div class="tv-head">
    <h2 class="section-title">TV SHOWS</h2>
    <div class="tv-arrows">
      <svg width="12" height="20" viewBox="0 0 12 20"><path d="M10 2 2 10l8 8" fill="none" stroke="#555" stroke-width="2.5"/></svg>
      <svg width="12" height="20" viewBox="0 0 12 20"><path d="M2 2l8 8-8 8" fill="none" stroke="#555" stroke-width="2.5"/></svg>
    </div>
  </div>
  <article class="show-card" style="left:430px">
    <div class="show-photo" role="img" aria-label="TV show still of the physician outdoors" style="background:linear-gradient(150deg,#8fae6a,#4d6b3a)">
      <svg width="70" height="70" viewBox="0 0 70 70"><circle cx="35" cy="35" r="33" fill="#fff"/><path d="M28 22v26l20-13z" fill="#333"/></svg>
    </div>
    <h3>FUSCE AT VESTIBULUM</h3>
    <p>Quisque euismod lobortis felis, ac tincidunt neque porta interdum accumsan sceleri sque vitae id ligula.</p>
    <a class="watch" href="#">WATCH VIDEO</a>
  </article>
  <article class="show-card" style="left:800px">
    <div class="show-photo" role="img" aria-label="TV show still of a panel discussion at a table" style="background:linear-gradient(150deg,#6f7f6a,#33403a)">
      <svg width="70" height="70" viewBox="0 0 70 70"><circle cx="35" cy="35" r="33" fill="#fff"/><path d="M28 22v26l20-13z" fill="#333"/></svg>
    </div>
    <h3>FUSCE AT VESTIBULUM</h3>
    <p>Quisque euismod lobortis felis, ac tincidunt neque porta interdum accumsan sceleri sque vitae id ligula.</p>
    <a class="watch" href="#">WATCH VIDEO</a>
  </article>
</section>

<section class="media">
  <div class="media-copy">
    <h2 class="section-title">ABOUT ME IN MEDIA</h2>
    <p class="body-copy">Benjamin Carver, DO, EMT-P, FAWM, is an assistant professor of emergency medicine and EMS at Coastal State University. He's an active EMS physician with multiple departments in Florida, including medical director for Bayline Fire Rescue Task Force One USAR and very active globally in wilderness/austere EMS.</p>
    <a class="btn btn-green" href="#">READ MORE</a>
  </div>
  <div class="round-photo" role="img" aria-label="Photo of the physician with a group at a community event"></div>
</section>

<section class="splits">
  <a class="split split-gallery" href="#" role="img" aria-label="Gallery tile with a group photo of the physician and colleagues"><span>GALLERY</span></a>
  <a class="split split-research" href="#" role="img" aria-label="Research tile with a photo of a field training scene"><span>RESEARCH</span></a>
  <a class="split split-television" href="#" role="img" aria-label="Television tile with a photo of a studio panel"><span>TELEVISION</span></a>
</section>

<footer class="site-footer">
  <div class="footer-row">
    <nav class="footer-nav">
      <a href="#">HOME</a><a href="#">EXPERIENCE</a><a href="#">CONSULTING</a><a href="#">LECTURES</a><a href="#">AFFILIATES</a><a href="#">CONTACT</a>
    </nav>
    <div class="social"><span></span><span></span><span></span><span></span><span></span></div>
  </div>
  <p class="copyright">Copyright © 2019, Company Name. All Rights Reserved.</p>
</footer>
</body>
</html>
```